PeakRoamJourneys

1. Can you describe what your company does?

Please find enclosed documents for your reference about our business doing.

2. Who are your target customers for the website?

Company Positioning: A comprehensive supplier of premier international sports travel and high-end event services.
Core Advantage: Exclusive international partnership resources and an Official Ticketing Assurance System.
Service Standard: One-Stop, High-Quality Service Solutions based on the "An once-in-a-lifetime experience" philosophy.

Our target customers for the website:
Mid-to-High-end Sports Enthusiasts
Corporate Clients
Sports Associations
Please kindly find enclosed for more details about our target customers, I think it's very important to make it clear to you.

3. Do you have an existing domain name / website address?

Yes, I have. I just applied for this new domain and it's totally a new website. www.peakroamjourneys.example

4. In addition to a Home Page, which other pages / sections would you like your website to have:
About Us
Contact Us , Office / Mailing Address
Sports Travel Products( Bucket Lists) : Globe Shield, Royal Quartet, Vantara Games, Football, Hoopline League, Golf, Skiing, Hiking,Galas
Reviews/ Unforgettable Moments
FAQs
Any other page / section you would like: Here is the website for your reference, www.lanewander.example
For each of the pages / sections you’d like to have, please provide the text (and images, if available) you would like to include.
Please recommend 2-3 templates to me, and let me know what kind of text I will provide to every web pages.

5. Which of the below are features and functionalities your website will need:
Image Gallery
Videos
Contact Form
Maps
FAQs
6. Please provide the URLs for the social media profiles you'd like to link to the website.

Do you know Bright Lantern App?

Please let me know anything you need, thank you very much!

Have a good day!

Target Market(s)

Travel for the world-wide sports games and make an once-in-a-lifetime experience

Industry/Entity Type

sports and travel industry

Coding

Number of Pages Required

5+ page

Requirements
Must have
• our logo
Nice to have
• On the homepage, I’d like a banner-style section to prominently showcase the latest products.

```html
<!DOCTYPE html>
<html lang="en">
<head>
<meta charset="utf-8">
<title>PeakRoamJourneys – Website Design</title>
<link href="https://fonts.googleapis.com/css2?family=Open+Sans:wght@400;600;700&display=swap" rel="stylesheet">
<style>
:root{
  --canvas:#f5f5f5;
  --bg:#222222;
  --bg-alt:#2b2b2b;
  --band:#333333;
  --card:#363636;
  --card-line:#444444;
  --field:#3a3a3a;
  --text:#ffffff;
  --muted:#c2c2c2;
  --accent:#4a72b8;
  --accent-soft:#6d8fd0;
}
*{box-sizing:border-box;margin:0;padding:0}
html,body{width:1200px;height:1200px;overflow:hidden;background:var(--canvas)}
body{font-family:"Open Sans",sans-serif;color:var(--text)}
.stage{position:absolute;left:0;top:0;width:1932px;height:1932px;transform:scale(.62112);transform-origin:0 0;background:var(--canvas)}
.abs{position:absolute}
.page{position:absolute;top:54px;width:451px;background:var(--bg);overflow:hidden}
.page-home{left:145px;height:1451px}
.page-services{left:693px;height:1821px}
.page-contact{left:1215px;height:875px}
.photo{position:absolute;border-radius:2px}
.title{position:absolute;left:0;width:100%;text-align:center;font-weight:700;font-size:13px}
.title::after{content:"";display:block;width:26px;height:1px;background:var(--accent);margin:5px auto 0}
.sub{position:absolute;left:0;width:100%;text-align:center;font-size:5px;color:var(--muted);line-height:1.8}
.txt{font-size:5px;color:var(--muted);line-height:1.8}
.btn{position:absolute;height:12px;border-radius:7px;background:var(--accent);font-size:4.5px;display:flex;align-items:center;justify-content:center;color:#fff}
.btn.ghost{background:transparent;border:1px solid var(--accent-soft)}
.card{position:absolute;background:var(--card);border:1px solid var(--card-line);border-radius:3px;overflow:hidden}
.card h4{font-size:6.5px;font-weight:700;margin:0 0 4px}
.card .price{font-size:5px;color:#fff;margin-top:5px}
.latest h4{font-size:5.5px;font-weight:700;margin-bottom:2px}
.latest .txt{font-size:4px;line-height:1.6}
.latest .price{font-size:5px;margin-top:5px}
.field{position:absolute;height:14px;background:var(--field);border:1px solid #555;border-radius:2px;font-size:4.5px;color:var(--muted);padding:0 5px;display:flex;align-items:center;justify-content:space-between}
.field::after{content:"";width:3px;height:3px;border-right:1px solid #ccc;border-bottom:1px solid #ccc;transform:rotate(45deg)}
.dot{display:inline-block;width:9px;height:9px;border-radius:50%;border:1px solid #666;margin-right:6px}
.icon{width:7px;height:7px;fill:var(--accent);vertical-align:middle;margin-right:4px}
.sport{position:absolute;width:62px;height:50px;background:#2f2f2f;border:1px solid #444;border-radius:3px;font-size:4.5px;text-align:center;padding-top:12px}
.sport svg{display:block;margin:0 auto 8px;width:12px;height:12px}
.faq{position:absolute;left:84px;width:282px;height:26px;background:#2c2c2c;border:1px solid #4a4a4a;border-radius:2px;font-size:5.5px;font-weight:600;padding:0 8px;display:flex;align-items:center;justify-content:space-between}
.faq::after{content:"";width:3px;height:3px;border-right:1px solid #ccc;border-bottom:1px solid #ccc;transform:rotate(45deg)}
.chip{display:inline-block;font-size:4.5px;padding:2px 7px;border-radius:6px;border:1px solid #555;margin-right:4px;color:#ddd}
.chip.on{background:var(--accent);border-color:var(--accent)}
.foot h5{font-size:6px;font-weight:700;margin-bottom:12px}
.foot p{font-size:4.5px;color:var(--muted);line-height:2.9}
.badge{width:50px;height:11px;border:1px solid #666;border-radius:2px;margin-top:8px}
.contact-list p{font-size:4.5px;color:var(--muted);margin-bottom:7px}
.feature{height:29px}
.feature h6{font-size:5.5px;font-weight:600}
.feature .txt{padding-left:14px;font-size:4.5px}
</style>
</head>
<body>
<div class="stage">

<section class="page page-home">
  <div class="abs" style="left:0;top:0;width:451px;height:14px;background:#111;font-size:4px;color:#ddd;display:flex;justify-content:flex-end;align-items:center;gap:14px;padding-right:4px">
    <span>▪ Official Tickets to Top Global Events</span><span>◦ Official Ticketing</span>
  </div>
  <nav class="abs" style="left:0;top:14px;width:451px;height:20px;background:#1a1a1a;font-size:3.8px;display:flex;align-items:center;gap:10px;padding-left:54px;color:#ddd">
    <span style="font-size:5px;font-weight:700">PeakRoamJourneys</span>
    <span>SPORTS</span><span>PACKAGES</span><span>DESTINATIONS</span><span>GROUP TRAVEL</span><span>GIFT CARDS</span><span>ABOUT</span><span>NEWS</span>
    <span style="margin-left:14px">○</span><span>●</span>
  </nav>
  <div class="photo" role="img" aria-label="Hero photo of a footballer in action under stadium lights" style="left:0;top:34px;width:451px;height:265px;background:radial-gradient(circle at 60% 30%,#3a3530,#141414 70%)"></div>
  <h1 class="abs" style="left:0;top:148px;width:224px;text-align:center;font-size:16px;line-height:1.25;font-weight:700">Once-In-A-Lifetime<br>Experiences</h1>
  <p class="abs txt" style="left:8px;top:193px;width:208px;text-align:center;color:#ddd">From VIP hospitality to personalized itineraries, we create unforgettable journeys that blend your passion for sports with luxury travel.</p>
  <div class="btn" style="left:62px;top:221px;width:46px">Our Services</div>
  <div class="btn ghost" style="left:112px;top:221px;width:48px">Plan Your Trip</div>
  <div class="abs" style="left:223px;top:152px;width:228px;height:90px;background:rgba(40,40,40,.85);border:1px solid #444;border-radius:3px">
    <div class="abs" style="left:0;top:10px;width:228px;text-align:center;font-size:6.5px;font-weight:600">Find Your Perfect Sports Experience</div>
    <div class="field" style="left:10px;top:30px;width:62px">Choose a Sport</div>
    <div class="field" style="left:81px;top:30px;width:62px">Select an Event</div>
    <div class="field" style="left:152px;top:30px;width:66px">Pick a Year</div>
    <div class="field" style="left:10px;top:49px;width:62px">Choose a Location</div>
    <div class="btn" style="left:85px;top:70px;width:58px;height:10px">FIND PACKAGES</div>
  </div>

  <div class="abs" style="left:0;top:299px;width:451px;height:181px;background:var(--bg-alt)"></div>
  <div class="abs" style="left:0;top:312px;width:451px;text-align:center;font-size:6.5px;font-weight:600">Latest Premium Experiences</div>
  <div class="card latest" style="left:22px;top:338px;width:100px;height:115px">
    <div class="photo" role="img" aria-label="Football resting in front of a goal net" style="left:0;top:0;width:100px;height:62px;background:linear-gradient(160deg,#d8c23a,#2a4fa0 55%,#c63d3d)"></div>
    <div class="abs" style="left:6px;top:68px;width:90px"><h4>Globe Shield 2026</h4><p class="txt">VIP hospitality packages with exclusive access</p><p class="price">From $5,000</p></div>
  </div>
  <div class="card latest" style="left:128px;top:338px;width:100px;height:115px">
    <div class="photo" role="img" aria-label="Sprinters racing on an outdoor track" style="left:0;top:0;width:100px;height:62px;background:linear-gradient(180deg,#9cb0c0,#6a7a5a 60%,#b0523a)"></div>
    <div class="abs" style="left:6px;top:68px;width:90px"><h4>Lawnfield Open 2024</h4><p class="txt">Centre Court tickets with exclusive player access</p><p class="price">From $3,500</p></div>
  </div>
  <div class="card latest" style="left:234px;top:338px;width:100px;height:115px">
    <div class="photo" role="img" aria-label="Athlete in teal light with a football" style="left:0;top:0;width:100px;height:62px;background:linear-gradient(150deg,#0f2a3a,#1a8a9a 55%,#0b1a25)"></div>
    <div class="abs" style="left:6px;top:68px;width:90px"><h4>Pinecrest Invitational 2024</h4><p class="txt">Exclusive access to golf's most prestigious tournament</p><p class="price">From $4,200</p></div>
  </div>
  <div class="card latest" style="left:340px;top:338px;width:100px;height:115px">
    <div class="photo" role="img" aria-label="Athlete leaping against a blue sky" style="left:0;top:0;width:100px;height:62px;background:linear-gradient(180deg,#1c3870,#3a5a9a)"></div>
    <div class="abs" style="left:6px;top:68px;width:90px"><h4>Seine 2024 Vantara Games</h4><p class="txt">Premium seating and luxury accommodations</p><p class="price">From $7,500</p></div>
  </div>
  <div class="abs" style="left:22px;top:462px;width:418px;height:2px;background:#444"><div style="width:93%;height:2px;background:var(--accent)"></div></div>

  <h2 class="abs" style="left:18px;top:511px;font-size:13px;font-weight:700">Why Choose PeakRoamJourneys</h2>
  <p class="abs txt" style="left:18px;top:538px;width:200px;color:#ddd">With over a decade of experience, we've perfected the art of creating unforgettable sports travel experiences that go beyond ordinary event attendance.</p>
  <div class="abs" style="left:18px;top:580px;width:210px">
    <div class="feature"><h6><svg class="icon" viewBox="0 0 10 10"><circle cx="5" cy="5" r="5"/></svg>Decades of Experience</h6><p class="txt">Over 15 years of industry expertise and insider knowledge</p></div>
    <div class="feature"><h6><svg class="icon" viewBox="0 0 10 10"><rect y="2" width="10" height="6"/></svg>Guaranteed Access</h6><p class="txt">Premium tickets and accommodations for high-demand events</p></div>
    <div class="feature"><h6><svg class="icon" viewBox="0 0 10 10"><path d="M5 0l1.5 3.5H10L7.2 5.8 8.2 10 5 7.6 1.8 10l1-4.2L0 3.5h3.5z"/></svg>Unique Experiences</h6><p class="txt">Behind-the-scenes access and exclusive opportunities</p></div>
    <div class="feature"><h6><svg class="icon" viewBox="0 0 10 10"><rect y="1" width="10" height="9" rx="1"/></svg>Personalized Itineraries</h6><p class="txt">Tailored travel agendas designed around your preferences</p></div>
    <div class="feature"><h6><svg class="icon" viewBox="0 0 10 10"><circle cx="5" cy="5" r="4" fill="none" stroke="#4a72b8" stroke-width="1.5"/></svg>24/7 Support</h6><p class="txt">Round-the-clock concierge service during your travels</p></div>
  </div>
  <div class="photo" role="img" aria-label="Floodlit cricket stadium at dusk" style="left:231px;top:541px;width:198px;height:142px;background:linear-gradient(180deg,#1d2f6a 0%,#3a4f8a 35%,#2f6a2f 60%,#4a8a3a 100%)"></div>

  <div class="title" style="top:771px">Browse by Sport</div>
  <div class="sub" style="top:796px">Explore our premium experiences across all major sports disciplines</div>
  <div class="sport" style="left:18px;top:823px"><svg viewBox="0 0 12 12"><ellipse cx="6" cy="6" rx="6" ry="4" fill="#fff"/></svg>Football</div>
  <div class="sport" style="left:88px;top:823px"><svg viewBox="0 0 12 12"><circle cx="6" cy="5" r="4" fill="#fff"/><rect x="5" y="9" width="2" height="3" fill="#fff"/></svg>Golf</div>
  <div class="sport" style="left:158px;top:823px"><svg viewBox="0 0 12 12"><circle cx="6" cy="6" r="5" fill="none" stroke="#fff" stroke-width="1.5"/><circle cx="6" cy="6" r="2" fill="#fff"/></svg>Soccer</div>
  <div class="sport" style="left:227px;top:823px"><svg viewBox="0 0 12 12"><circle cx="5" cy="5" r="4" fill="#fff"/><circle cx="10" cy="10" r="2" fill="#fff"/></svg>Tennis</div>
  <div class="sport" style="left:297px;top:823px"><svg viewBox="0 0 12 12"><circle cx="6" cy="6" r="5.5" fill="#fff"/><path d="M0.5 6h11M6 .5v11" stroke="#2f2f2f"/></svg>Basketball</div>
  <div class="sport" style="left:366px;top:823px"><svg viewBox="0 0 12 12"><ellipse cx="6" cy="4" rx="5" ry="2.5" fill="#fff"/><rect x="1" y="6" width="10" height="3" rx="1.5" fill="#fff"/></svg>Hockey</div>
  <div class="sport" style="left:18px;top:881px"><svg viewBox="0 0 12 12"><circle cx="6" cy="6" r="5.5" fill="#fff"/></svg>Baseball</div>
  <div class="sport" style="left:88px;top:881px"><svg viewBox="0 0 12 12"><rect x="1" y="1" width="10" height="8" fill="none" stroke="#fff"/><rect x="1" y="1" width="3" height="3" fill="#fff"/><rect x="7" y="4" width="3" height="3" fill="#fff"/></svg>Motorsports</div>
  <div class="sport" style="left:158px;top:881px"><svg viewBox="0 0 12 12"><circle cx="6" cy="8" r="3.5" fill="none" stroke="#fff" stroke-width="1.5"/><path d="M3 0l3 4 3-4" fill="none" stroke="#fff" stroke-width="1.5"/></svg>Vantara Games</div>
  <div class="sport" style="left:227px;top:881px"><svg viewBox="0 0 12 12"><path d="M2 12V6l4-5 4 2v3H5v6z" fill="#fff"/></svg>Horse Racing</div>
  <div class="sport" style="left:297px;top:881px;padding-top:32px">Rugby</div>
  <div class="sport" style="left:366px;top:881px;padding-top:32px">Cricket</div>

  <div class="title" style="top:986px">About Us</div>
  <div class="sub" style="top:1012px;left:95px;width:261px">Established in 2009, we've been creating once-in-a-lifetime sports experiences for over a decade.</div>
  <h3 class="abs" style="left:18px;top:1050px;width:200px;font-size:10px;line-height:1.7;font-weight:600">Premier Sports Travel &amp; Event Management Expert</h3>
  <p class="abs txt" style="left:18px;top:1093px;width:200px">Our company has been deeply rooted in the sports and high-end service sector for over a decade, with businesses covering High-end Conference Management and Planning, Sports Event Operation, and, at its core, Sports Travel services.</p>
  <p class="abs txt" style="left:18px;top:1139px;width:200px">Our mission is to create an "An once-in-a-lifetime experience" for our clients by focusing on top-tier international events and providing one-stop, high-quality service solutions.</p>
  <div class="card" style="left:18px;top:1184px;width:93px;height:102px;padding:14px 7px 0">
    <svg viewBox="0 0 12 8" style="display:block;margin:0 auto 10px;width:14px;height:9px"><rect width="12" height="8" rx="1" fill="#4a72b8"/></svg>
    <h4 style="text-align:center">Official Ticketing</h4><p class="txt" style="font-size:4.5px">Guaranteed access to premium events with official ticket assurance.</p>
  </div>
  <div class="card" style="left:122px;top:1184px;width:92px;height:102px;padding:14px 7px 0">
    <svg viewBox="0 0 14 8" style="display:block;margin:0 auto 10px;width:16px;height:9px"><path d="M0 4l4-4 3 2 3-2 4 4-4 4H4z" fill="#4a72b8"/></svg>
    <h4 style="text-align:center">Global Partnerships</h4><p class="txt" style="font-size:4.5px">Exclusive relationships with international sports organizations.</p>
  </div>
  <div class="card" style="left:18px;top:1298px;width:93px;height:102px;padding:14px 7px 0">
    <svg viewBox="0 0 12 8" style="display:block;margin:0 auto 10px;width:14px;height:9px"><path d="M1 7a5 5 0 0 1 10 0zM0 7h12v1H0z" fill="#4a72b8"/></svg>
    <h4 style="text-align:center">Premium Service</h4><p class="txt" style="font-size:4.5px">One-stop solutions for the ultimate sports travel experience.</p>
  </div>
  <div class="abs" style="left:232px;top:1153px;width:197px;height:142px;background:#333;border:1px solid #444;border-radius:3px">
    <svg viewBox="0 0 24 24" class="abs" style="left:86px;top:60px;width:24px;height:24px"><circle cx="12" cy="12" r="11" fill="#eee"/><path d="M9.5 7.5v9l7-4.5z" fill="#333"/></svg>
    <p class="abs" style="left:0;top:126px;width:197px;text-align:center;font-size:4.5px;color:#ddd">Video Placeholder - Your Video Will Appear Here</p>
  </div>
</section>

<section class="page page-services">
  <div class="title" style="top:22px">Our Services</div>
  <div class="sub" style="top:46px;left:105px;width:241px">Tailored experiences for different client segments with our exclusive partnerships and official ticketing system.</div>
  <div class="card" style="left:30px;top:81px;width:122px;height:153px">
    <div class="photo" role="img" aria-label="Sprinter in starting blocks on a red track" style="left:0;top:0;width:122px;height:68px;background:linear-gradient(180deg,#b84a3a,#8a3025)"></div>
    <div class="abs" style="left:8px;top:77px;width:108px"><h4>Sports Enthusiasts</h4><p class="txt" style="font-size:4.5px">For individuals seeking ultimate experiences with official, scarce seats for top-tier global events and personalized services.</p></div>
    <div class="btn" style="left:8px;top:128px;width:46px">Learn More</div>
  </div>
  <div class="card" style="left:163px;top:81px;width:122px;height:153px">
    <div class="photo" role="img" aria-label="Business team meeting in an office" style="left:0;top:0;width:122px;height:68px;background:linear-gradient(180deg,#cfcac4,#7a746c)"></div>
    <div class="abs" style="left:8px;top:77px;width:108px"><h4>Corporate Clients</h4><p class="txt" style="font-size:4.5px">High-end incentive programs, conference services, and reliable event operations for businesses.</p></div>
    <div class="btn" style="left:8px;top:128px;width:46px">Learn More</div>
  </div>
  <div class="card" style="left:296px;top:81px;width:122px;height:153px">
    <div class="photo" role="img" aria-label="Athlete training on a mat" style="left:0;top:0;width:122px;height:68px;background:linear-gradient(180deg,#eeeeee,#d0b0a0)"></div>
    <div class="abs" style="left:8px;top:77px;width:108px"><h4>Sports Associations</h4><p class="txt" style="font-size:4.5px">Professional team travel, overseas competition support, and event operation services.</p></div>
    <div class="btn" style="left:8px;top:128px;width:46px">Learn More</div>
  </div>

  <div class="title" style="top:293px">Featured Experiences</div>
  <div class="sub" style="top:317px;left:105px;width:241px">Our curated selection of premium sports travel packages for the world's most prestigious events.</div>
  <div class="abs" style="left:0;top:353px;width:451px;text-align:center"><span class="chip on">All Events</span><span class="chip">Football</span><span class="chip">Tennis</span><span class="chip">Basketball</span><span class="chip">Vantara Games</span><span class="chip">Golf</span></div>
  <div class="card" style="left:30px;top:378px;width:122px;height:137px"><div class="photo" role="img" aria-label="Football in front of a goal net" style="left:0;top:0;width:122px;height:68px;background:linear-gradient(160deg,#d8c23a,#2a4fa0 55%,#3a8a3a)"></div><div class="abs" style="left:7px;top:76px;width:110px"><h4>Globe Shield</h4><p class="txt" style="font-size:4.5px">Experience the world's biggest football tournament with VIP access and premium hospitality.</p><p class="price">From $5,000</p></div></div>
  <div class="card" style="left:163px;top:378px;width:122px;height:137px"><div class="photo" role="img" aria-label="Tennis player in teal light" style="left:0;top:0;width:122px;height:68px;background:linear-gradient(150deg,#0f3040,#1f8a90 50%,#c86a30)"></div><div class="abs" style="left:7px;top:76px;width:110px"><h4>Lawnfield Open Championships</h4><p class="txt" style="font-size:4.5px">Premium tickets to the world's most prestigious tennis tournament with exclusive access.</p><p class="price">From $3,500</p></div></div>
  <div class="card" style="left:296px;top:378px;width:122px;height:137px"><div class="photo" role="img" aria-label="Basketball dropping through a hoop" style="left:0;top:0;width:122px;height:68px;background:radial-gradient(circle at 30% 70%,#a04020,#1a1410 60%)"></div><div class="abs" style="left:7px;top:76px;width:110px"><h4>Hoopline League Finals</h4><p class="txt" style="font-size:4.5px">Courtside seats and premium experiences for basketball's championship series.</p><p class="price">From $2,800</p></div></div>
  <div class="card" style="left:30px;top:526px;width:122px;height:129px"><div class="photo" role="img" aria-label="Sprinters on an outdoor track" style="left:0;top:0;width:122px;height:68px;background:linear-gradient(180deg,#9cb0c0,#6a7a5a 60%,#b0523a)"></div><div class="abs" style="left:7px;top:76px;width:110px"><h4>Summer Vantara Games</h4><p class="txt" style="font-size:4.5px">Comprehensive packages for the world's greatest sporting spectacle.</p><p class="price">From $7,500</p></div></div>
  <div class="card" style="left:163px;top:526px;width:122px;height:129px"><div class="photo" role="img" aria-label="Athlete in teal light with a ball" style="left:0;top:0;width:122px;height:68px;background:linear-gradient(150deg,#0f2a3a,#1a8a9a 55%,#0b1a25)"></div><div class="abs" style="left:7px;top:76px;width:110px"><h4>Pinecrest Invitational</h4><p class="txt" style="font-size:4.5px">Exclusive access to golf's most prestigious tournament at Pinecrest National.</p><p class="price">From $4,200</p></div></div>
  <div class="card" style="left:296px;top:526px;width:122px;height:129px"><div class="photo" role="img" aria-label="Football on a grass pitch in sunlight" style="left:0;top:0;width:122px;height:68px;background:linear-gradient(180deg,#6a7a50,#3a6a2a)"></div><div class="abs" style="left:7px;top:76px;width:110px"><h4>Continental Club Cup</h4><p class="txt" style="font-size:4.5px">VIP experiences for the continent's elite club football competition.</p><p class="price">From $2,500</p></div></div>

  <div class="abs" style="left:0;top:692px;width:451px;height:1px;background:#2e2e2e"></div>
  <div class="title" style="top:719px">Client Testimonials</div>
  <div class="sub" style="top:744px">Hear from our satisfied clients about their unforgettable sports travel experiences.</div>
  <div class="abs" style="left:20px;top:771px;width:410px;height:79px;background:#333;border:1px solid #444;border-radius:3px;padding:10px 11px">
    <p style="font-size:4.8px;font-style:italic;color:#ddd;line-height:1.8">"The Globe Shield experience arranged by PeakRoamJourneys was absolutely incredible. From premium seats to exclusive hospitality, every detail was perfect. Truly a once-in-a-lifetime experience!"</p>
    <div style="display:flex;align-items:center;margin-top:6px"><span style="width:14px;height:14px;border-radius:50%;background:#8a6a5a;margin-right:8px" role="img" aria-label="Client portrait"></span><div><p style="font-size:5px">Daniel Reyes</p><p style="font-size:4px;color:var(--muted)">Corporate Executive</p></div></div>
    <p style="font-size:4.5px;color:var(--accent-soft);margin-top:4px">Read More</p>
  </div>
  <div class="btn" style="left:194px;top:862px;width:32px">Previous</div>
  <div class="btn" style="left:233px;top:862px;width:24px">Next</div>

  <div class="title" style="top:936px">Gallery</div>
  <div class="sub" style="top:961px">Take a visual journey through our premium sports travel experiences.</div>
  <div class="photo" role="img" aria-label="Pitch line on green grass" style="left:20px;top:988px;width:99px;height:89px;background:linear-gradient(150deg,#6aa040,#3a7a2a)"></div>
  <div class="photo" role="img" aria-label="Football on grass" style="left:124px;top:988px;width:99px;height:89px;background:linear-gradient(180deg,#5a8a3a,#3a6a2a)"></div>
  <div class="photo" role="img" aria-label="Cyclists racing in a pack" style="left:228px;top:988px;width:99px;height:89px;background:linear-gradient(180deg,#8aa0b0,#3a5a8a 60%,#5a5a5a)"></div>
  <div class="photo" role="img" aria-label="Sprinter in blocks on a red track" style="left:332px;top:988px;width:98px;height:89px;background:linear-gradient(180deg,#b84a3a,#8a3025)"></div>
  <div class="photo" role="img" aria-label="Runners silhouetted against a blue sky" style="left:20px;top:1083px;width:99px;height:88px;background:linear-gradient(180deg,#3a7ab0,#0f2a4a)"></div>
  <div class="photo" role="img" aria-label="Floodlit stadium at night" style="left:124px;top:1083px;width:99px;height:88px;background:linear-gradient(180deg,#1d2f6a,#3a4f8a 40%,#3a7a3a)"></div>
  <div class="photo" role="img" aria-label="Hikers on a mountain trail" style="left:228px;top:1083px;width:99px;height:88px;background:linear-gradient(180deg,#a0aab8,#6a7a5a 55%,#5a6a3a)"></div>
  <div class="photo" role="img" aria-label="Sprinter in blocks on a red track" style="left:332px;top:1083px;width:98px;height:88px;background:linear-gradient(180deg,#b84a3a,#8a3025)"></div>
  <p class="abs" style="left:0;top:1188px;width:451px;text-align:center;font-size:5px;color:var(--accent-soft)">View More</p>

  <div class="title" style="top:1258px">Frequently Asked Questions</div>
  <div class="sub" style="top:1283px">Find answers to common questions about our sports travel services.</div>
  <div class="faq" style="top:1310px">How do you guarantee official tickets to premium events?</div>
  <div class="faq" style="top:1343px">What makes your service different from other sports travel agencies?</div>
  <div class="faq" style="top:1376px">Do you offer services for corporate clients?</div>
  <div class="faq" style="top:1409px">Can you arrange professional training experiences alongside event attendance?</div>
  <div class="faq" style="top:1442px">What is your cancellation and refund policy?</div>

  <div class="title" style="top:1537px">Contact Us</div>
  <div class="sub" style="top:1562px">Get in touch to start planning your ultimate sports travel experience.</div>
  <h4 class="abs" style="left:20px;top:1590px;font-size:7px;font-weight:600">Get In Touch</h4>
  <div class="abs contact-list" style="left:20px;top:1610px">
    <p><svg class="icon" viewBox="0 0 10 10"><path d="M5 0a3.5 3.5 0 0 1 3.5 3.5C8.5 6 5 10 5 10S1.5 6 1.5 3.5A3.5 3.5 0 0 1 5 0z"/></svg>48 Harbor Lane, Eastport, NY 10077</p>
    <p><svg class="icon" viewBox="0 0 10 10"><path d="M2 0l2 2-1 2 3 3 2-1 2 2-2 2C4 10 0 6 0 2z"/></svg>+1 (555) 010-2846</p>
    <p><svg class="icon" viewBox="0 0 10 10"><rect y="1.5" width="10" height="7"/></svg>hello@peakroamjourneys.example</p>
    <p><svg class="icon" viewBox="0 0 10 10"><circle cx="5" cy="5" r="5"/></svg>Mon - Fri: 9:00 AM - 6:00 PM</p>
    <p style="margin-top:4px"><span class="dot"></span><span class="dot"></span><span class="dot"></span><span class="dot"></span></p>
  </div>
  <div class="field" style="left:234px;top:1590px;width:196px">Your Name</div>
  <div class="field" style="left:234px;top:1614px;width:196px">Your Email</div>
  <div class="field" style="left:234px;top:1638px;width:196px">Your Phone</div>
  <div class="field" style="left:234px;top:1662px;width:196px">Interested In</div>
  <div class="field" style="left:234px;top:1686px;width:196px;height:52px;align-items:flex-start;padding-top:5px">Your Message</div>
  <div class="btn" style="left:234px;top:1749px;width:52px">Send Message</div>
</section>

<section class="page page-contact">
  <div class="title" style="top:41px">Contact Us</div>
  <div class="sub" style="top:64px">Get in touch to start planning your ultimate sports travel experience.</div>
  <h4 class="abs" style="left:29px;top:91px;font-size:7px;font-weight:600">Get In Touch</h4>
  <div class="abs contact-list" style="left:29px;top:110px">
    <p><svg class="icon" viewBox="0 0 10 10"><path d="M5 0a3.5 3.5 0 0 1 3.5 3.5C8.5 6 5 10 5 10S1.5 6 1.5 3.5A3.5 3.5 0 0 1 5 0z"/></svg>48 Harbor Lane, Eastport, NY 10077</p>
    <p><svg class="icon" viewBox="0 0 10 10"><path d="M2 0l2 2-1 2 3 3 2-1 2 2-2 2C4 10 0 6 0 2z"/></svg>+1 (555) 010-2846</p>
    <p><svg class="icon" viewBox="0 0 10 10"><rect y="1.5" width="10" height="7"/></svg>hello@peakroamjourneys.example</p>
    <p><svg class="icon" viewBox="0 0 10 10"><circle cx="5" cy="5" r="5"/></svg>Mon - Fri: 9:00 AM - 6:00 PM</p>
    <p style="margin-top:4px"><span class="dot"></span><span class="dot"></span><span class="dot"></span><span class="dot"></span></p>
  </div>
  <div class="field" style="left:234px;top:90px;width:188px">Your Name</div>
  <div class="field" style="left:234px;top:113px;width:188px">Your Email</div>
  <div class="field" style="left:234px;top:136px;width:188px">Your Phone</div>
  <div class="field" style="left:234px;top:159px;width:188px">Interested In</div>
  <div class="field" style="left:234px;top:182px;width:188px;height:51px;align-items:flex-start;padding-top:5px">Your Message</div>
  <div class="btn" style="left:234px;top:243px;width:50px">Send Message</div>
  <div class="photo" role="img" aria-label="Street map showing the office location" style="left:29px;top:273px;width:393px;height:136px;background:linear-gradient(135deg,#e8e6e0,#dfe3e8 60%,#cfe2c8);border-radius:3px"></div>

  <div class="abs" style="left:0;top:448px;width:451px;height:71px;background:var(--band)"></div>
  <div class="sub" style="top:455px;left:120px;width:211px">Subscribe to our newsletter for exclusive offers, event updates, and sports travel insights</div>
  <div class="abs" style="left:141px;top:483px;width:125px;height:14px;background:#2a2a2a;border:1px solid #444;font-size:4.5px;color:var(--muted);padding:4px 5px">Enter your email address</div>
  <div class="btn" style="left:270px;top:484px;width:40px">Subscribe</div>

  <h2 class="abs" style="left:0;top:557px;width:451px;text-align:center;font-size:12.5px;font-weight:700">Ready for Your Ultimate Sports Experience?</h2>
  <div class="sub" style="top:583px;left:108px;width:235px">Contact us today to start planning your unforgettable journey to the world's premier sporting events.</div>
  <div class="btn" style="left:200px;top:613px;width:51px;height:14px">Get In Touch</div>

  <div class="abs" style="left:0;top:663px;width:451px;height:212px;background:#2c2c2c;border-top:1px solid #3a3a3a"></div>
  <div class="abs foot" style="left:29px;top:689px;width:66px">
    <h5>PeakRoamJourneys</h5>
    <p style="line-height:1.8">Your premier partner for exclusive international sports travel and high-end event services since 2009.</p>
    <p>☏ 1-800-555-0147</p>
    <p><span class="dot"></span><span class="dot"></span><span class="dot"></span></p>
    <p><span class="dot"></span><span class="dot"></span></p>
    <div class="badge"></div><div class="badge"></div><div class="badge"></div>
  </div>
  <div class="abs foot" style="left:110px;top:689px"><h5>Sports</h5><p>Football<br>Golf<br>Soccer<br>Tennis<br>Basketball<br>View All Sports</p></div>
  <div class="abs foot" style="left:191px;top:689px"><h5>Destinations</h5><p>United States<br>Canada<br>Europe<br>Asia<br>Australia<br>View All Destinations</p></div>
  <div class="abs foot" style="left:272px;top:689px"><h5>Company</h5><p>About Us<br>How It Works<br>Our Services<br>Testimonials<br>Careers<br>Contact Us</p></div>
  <div class="abs foot" style="left:353px;top:689px"><h5>Support</h5><p>FAQ<br>Booking Terms<br>Privacy Policy<br>Terms of Service<br>Travel Insurance<br>Site Map</p></div>
</section>

</div>
</body>
</html>
```